Homemaking training schools needs a Business Card design

Designer, Hello!

No special requirements, good-looking enough.
--------------------------------------------------------------------------

Name: Marcus Dole
Chairman
Tel: 0574-71948263
Mobile: 13857420916
Email: kelvora@mailnest.example
Web: www.prt2019.example
Add: No.258, LanpingJie, BeiyuanQu, Ningbo, Zhejiang

LOGO
Ningbo PRT Homemaking Training School

Target Market(s)

pregnant women, mothers, infants, the elderly and families, including cleaning, cooking, nursing training.

Industry/Entity Type

Business

Contact Information for Business Card

Name: Marcus Dole
Chairman
Tel: 0574-71948263
Mobile: 13857420916
Email: kelvora@mailnest.example
Web: www.prt2019.example

LOGO

Font styles to use
Serif
Sans Serif
Decorative

Requirements
Nice to have
• Feels: clean, specifications, safety, comfort, warmth and happiness.

```html
<!DOCTYPE html>
<html lang="en">
<head>
<meta charset="utf-8">
<title>PinRuiTang Business Card</title>
<link rel="stylesheet" href="https://fonts.googleapis.com/css2?family=Lato:wght@400;700&family=Quicksand:wght@500;700&display=swap">
<style>
  :root {
    --brand-blue: #3877bb;
    --brand-pink: #e0167f;
    --pink-light: #f28cc0;
    --card-white: #ffffff;
    --ink-grey: #555a60;
    --stage: #e9eaec;
  }
  * { box-sizing: border-box; margin: 0; padding: 0; }
  html, body { width: 1200px; height: 900px; overflow: hidden; background: var(--stage); }
  .canvas { position: relative; width: 1200px; height: 900px; }

  .card {
    position: absolute; left: 250px; width: 700px; height: 390px;
    overflow: hidden; box-shadow: 0 6px 18px rgba(0,0,0,.18);
  }
  .card--back { top: 45px; background: var(--brand-blue); }
  .card--front { top: 465px; }
  .card__bg { position: absolute; inset: 0; }

  .wordmark {
    position: absolute; display: flex; align-items: flex-end; gap: 10px;
    font-family: 'Lato', sans-serif; font-weight: 700; letter-spacing: 1px;
  }
  .wordmark__dot { width: 22px; height: 22px; border-radius: 50%; background: var(--brand-pink); margin-bottom: 38px; }
  .tagline {
    position: absolute; display: flex; align-items: center; gap: 12px;
    font-family: 'Quicksand', sans-serif; font-weight: 500; letter-spacing: 1px;
  }
  .tagline__rule { height: 1.5px; width: 80px; }

  .card--back .wordmark { left: 190px; top: 120px; font-size: 56px; color: var(--card-white); }
  .card--back .tagline { left: 150px; top: 212px; font-size: 22px; color: var(--card-white); }
  .card--back .tagline__rule { background: var(--card-white); width: 95px; }
  .card--back .web {
    position: absolute; left: 0; right: 0; top: 272px; text-align: center;
    font-family: 'Lato', sans-serif; font-size: 17px; letter-spacing: 3px; color: var(--card-white);
  }

  .card--front .wordmark { left: 420px; top: 150px; font-size: 42px; color: var(--brand-blue); }
  .card--front .wordmark__dot { width: 18px; height: 18px; margin-bottom: 30px; }
  .card--front .tagline { left: 400px; top: 222px; font-size: 16px; color: var(--ink-grey); }
  .card--front .tagline__rule { background: var(--ink-grey); width: 55px; }

  .contact { position: absolute; left: 38px; top: 40px; color: var(--card-white); font-family: 'Lato', sans-serif; }
  .contact__name { font-size: 27px; font-weight: 700; }
  .contact__title { font-size: 15px; color: var(--brand-pink); margin-top: 2px; }
  .contact__address { font-size: 15px; line-height: 1.35; margin-top: 16px; }
  .contact__list { list-style: none; margin-top: 16px; font-size: 15px; }
  .contact__list li { display: flex; align-items: center; gap: 10px; height: 24px; }
  .contact__icon { width: 14px; height: 14px; flex: none; }
  .contact__list .no-icon { padding-left: 24px; }
</style>
</head>
<body>
<div class="canvas">

  <section class="card card--back">
    <div class="wordmark"><span>PinRuiTang</span><span class="wordmark__dot"></span></div>
    <div class="tagline"><span class="tagline__rule"></span><span>Training &amp; Services</span><span class="tagline__rule"></span></div>
    <p class="web">www.prt2019.example</p>
  </section>

  <section class="card card--front">
    <svg class="card__bg" width="700" height="390" viewBox="0 0 700 390">
      <defs>
        <linearGradient id="pinkSweep" x1="0" y1="0" x2="1" y2="0">
          <stop offset="0" stop-color="var(--brand-pink)"/>
          <stop offset="0.6" stop-color="var(--pink-light)"/>
          <stop offset="1" stop-color="var(--brand-pink)"/>
        </linearGradient>
      </defs>
      <rect width="700" height="390" fill="var(--brand-blue)"/>
      <path d="M345 0 Q190 200 340 390 L700 390 L700 0 Z" fill="url(#pinkSweep)"/>
      <path d="M378 0 Q228 200 360 390 L700 390 L700 0 Z" fill="var(--brand-blue)"/>
      <path d="M392 0 Q244 200 372 390 L700 390 L700 0 Z" fill="var(--card-white)"/>
    </svg>

    <div class="contact">
      <p class="contact__name">Marcus Dole</p>
      <p class="contact__title">Chairman</p>
      <p class="contact__address">No.258, LanpingJie<br>BeiyuanQu, Ningbo, Zhejiang</p>
      <ul class="contact__list">
        <li><svg class="contact__icon" viewBox="0 0 14 14"><path d="M3 1 L5 4 L4 5.5 Q5.5 8.5 8.5 10 L10 9 L13 11 L11.5 13 Q5 12.5 1 3 Z" fill="var(--brand-pink)"/></svg>0574-71948263</li>
        <li><svg class="contact__icon" viewBox="0 0 14 14"><rect x="3.5" y="1" width="7" height="12" rx="1.5" fill="var(--brand-pink)"/><rect x="5" y="3" width="4" height="6" fill="var(--brand-blue)"/></svg>13857420916</li>
        <li><svg class="contact__icon" viewBox="0 0 14 14"><rect x="1" y="3" width="12" height="8" fill="var(--brand-pink)"/><path d="M1 3 L7 8 L13 3" stroke="var(--brand-blue)" stroke-width="1.2" fill="none"/></svg>kelvora@mailnest.example</li>
        <li><svg class="contact__icon" viewBox="0 0 14 14"><circle cx="7" cy="7" r="6" fill="var(--brand-pink)"/><path d="M1 7 H13 M7 1 V13 M3 3.5 Q7 5 11 3.5 M3 10.5 Q7 9 11 10.5" stroke="var(--brand-blue)" stroke-width="0.9" fill="none"/></svg>www.prt2019.example</li>
      </ul>
    </div>

    <div class="wordmark"><span>PinRuiTang</span><span class="wordmark__dot"></span></div>
    <div class="tagline"><span class="tagline__rule"></span><span>Training &amp; Services</span><span class="tagline__rule"></span></div>
  </section>

</div>
</body>
</html>
```